Letterhead Design Project

I would like some modern, youthful, yet professional.

Industry/Entity Type

It Professional

Requirements
Must have
• On the left side the names of the Planning Committee:
Planning Committee
Founding Leaders:
Dorvena Pike, RISE Youngsters - Washington, DC
Marisol Trevane, RISE Youngsters - Washington, DC
Benedira Coltrop, RISE Youngsters - Washington, DC
Gregory Ashfield, RISE Youngsters - Washington, DC
Wren Talbek, Alliance of Northern Prairie Young People Support Circle
Petra Vondrakova, Alliance of Northern Prairie Young People Support Circle
Rosalind Burke, Countrywide Young People Support Circle, Canada
Irit Glen Shoval, Countrywide Young People Support Circle, Canada
Chair
Kendra Oduya, RISE Youngsters, Washington, DC
Co-Chairs
Ruth Palmquist, Global Guardian Homes Association, Amsterdam. Netherlands
Tessa Whitlow, Bright Pathway Partners, Jackson, MS
Owen Strade, Martha J Peller Trust

```html
<!DOCTYPE html>
<html lang="en">
<head>
<meta charset="utf-8">
<title>Planning Committee Letterhead</title>
<link rel="stylesheet" href="https://fonts.googleapis.com/css2?family=Mulish:wght@400;700&display=swap">
<style>
  :root {
    --navy-deep: #0a2d6e;
    --navy: #123f8f;
    --blue-bright: #1f5bb8;
    --paper: #ffffff;
    --ink-light: #ffffff;
    --ink-blue: #1a4a9c;
    --glow: rgba(255,255,255,0.16);
  }
  * { margin: 0; padding: 0; box-sizing: border-box; }
  html, body { width: 900px; height: 1200px; overflow: hidden; background: var(--paper); }
  .letterhead {
    position: relative;
    width: 900px;
    height: 1200px;
    background: var(--paper);
    font-family: "Mulish", sans-serif;
    overflow: hidden;
  }
  .header-band, .footer-band { position: absolute; left: 0; width: 900px; }
  .header-band { top: 0; height: 400px; }
  .footer-band { bottom: 0; height: 260px; }
  .globe-decoration {
    position: absolute;
    left: -40px;
    top: 200px;
    width: 260px;
    height: 150px;
    border-radius: 50%;
    background: radial-gradient(ellipse at center, var(--glow) 0%, rgba(255,255,255,0.05) 55%, rgba(255,255,255,0) 72%);
  }
  .committee {
    position: absolute;
    top: 16px;
    color: var(--ink-light);
    font-size: 10.5px;
    line-height: 13.6px;
  }
  .committee--founders { left: 6px; }
  .committee--chairs { left: 440px; }
  .committee p { white-space: nowrap; }
  .committee .member-name { font-weight: 700; }
  .partner {
    position: absolute;
    display: flex;
    align-items: center;
    gap: 6px;
    font-family: "Mulish", sans-serif;
    font-weight: 700;
    white-space: nowrap;
  }
  .partner--on-paper { color: var(--ink-blue); }
  .partner--on-band { color: var(--ink-light); }
  .partner-mark-circle { width: 22px; height: 22px; border-radius: 50%; flex: none; }
  .partner-mark-square { width: 20px; height: 20px; flex: none; }
  .partner--on-paper .partner-mark-circle,
  .partner--on-paper .partner-mark-square { background: var(--blue-bright); }
  .partner--on-band .partner-mark-circle,
  .partner--on-band .partner-mark-square { background: var(--ink-light); }
  .partner-summit { left: 8px; top: 1150px; font-size: 10px; line-height: 12px; width: 140px; white-space: normal; }
  .partner-pathway { left: 162px; top: 1152px; font-size: 10px; width: 90px; white-space: normal; line-height: 12px; }
  .partner-guardian { left: 258px; top: 1156px; font-size: 15px; }
  .partner-rise { left: 398px; top: 1160px; font-size: 17px; }
  .partner-belcourt { left: 512px; top: 1163px; font-size: 14px; }
  .partner-peller { left: 720px; top: 1166px; font-size: 13px; font-weight: 400; }
</style>
</head>
<body>
<main class="letterhead">
  <svg class="header-band" viewBox="0 0 900 400" aria-hidden="true">
    <defs>
      <linearGradient id="headerFill" x1="0" y1="0" x2="1" y2="1">
        <stop offset="0" stop-color="#163f86"/>
        <stop offset="0.55" stop-color="#0d3274"/>
        <stop offset="1" stop-color="#1a4fa3"/>
      </linearGradient>
    </defs>
    <path d="M0 0 H900 V130 C820 138 740 150 660 168 C560 190 470 205 400 240 C300 290 150 330 0 365 Z" fill="url(#headerFill)"/>
  </svg>
  <div class="globe-decoration" role="img" aria-label="Faint globe swirl decoration"></div>

  <section class="committee committee--founders">
    <p>Planning Committee</p>
    <p>Founding Leaders:</p>
    <p><span class="member-name">Dorvena Pike</span>, RISE Youngsters - Washington, DC</p>
    <p><span class="member-name">Marisol Trevane</span>, RISE Youngsters - Washington, DC</p>
    <p><span class="member-name">Benedira Coltrop</span>, RISE Youngsters - Washington, DC</p>
    <p><span class="member-name">Gregory Ashfield</span>, RISE Youngsters - Washington, DC</p>
    <p><span class="member-name">Wren Talbek</span>, Alliance of Northern Prairie Young People Support Circle</p>
    <p><span class="member-name">Petra Vondrakova</span>, Alliance of Northern Prairie Young People Support Circle</p>
    <p><span class="member-name">Rosalind Burke</span>, Countrywide Young People Support Circle, Canada</p>
    <p><span class="member-name">Irit Glen Shoval</span>, Countrywide Young People Support Circle, Canada</p>
  </section>

  <section class="committee committee--chairs">
    <p>Chair</p>
    <p><span class="member-name">Kendra Oduya</span>, RISE Youngsters, Washington, DC</p>
    <p>Co-Chairs</p>
    <p><span class="member-name">Ruth Palmquist</span>, Global Guardian Homes Association, Amsterdam. Netherlands</p>
    <p><span class="member-name">Tessa Whitlow</span>, Bright Pathway Partners, Jackson, MS</p>
    <p><span class="member-name">Owen Strade</span>, Martha J Peller Trust</p>
  </section>

  <svg class="footer-band" viewBox="0 0 900 260" aria-hidden="true">
    <defs>
      <linearGradient id="footerFill" x1="0" y1="0" x2="1" y2="1">
        <stop offset="0" stop-color="#0b2b6a"/>
        <stop offset="1" stop-color="#1b54ab"/>
      </linearGradient>
    </defs>
    <path d="M360 260 C390 170 470 130 600 105 C720 82 820 65 900 58 V260 Z" fill="url(#footerFill)"/>
  </svg>

  <div class="partner partner--on-paper partner-summit"><span class="partner-mark-circle"></span><span>2013 Global Gathering of Young People</span></div>
  <div class="partner partner--on-paper partner-pathway"><span>Bright Pathway Partners</span></div>
  <div class="partner partner--on-paper partner-guardian"><span class="partner-mark-square"></span><span>GGHA</span></div>
  <div class="partner partner--on-band partner-rise"><span class="partner-mark-circle"></span><span>RISE</span></div>
  <div class="partner partner--on-band partner-belcourt"><span class="partner-mark-circle"></span><span>Belcourt Family Fund</span></div>
  <div class="partner partner--on-band partner-peller"><span>Martha J Peller Trust</span></div>
</main>
</body>
</html>
```